Profesional personal website needs design and business card

I need a business card with my professional name as a logo "Dorian Vitality" for my business. I am a Wellness Coach, consultant and trainer. So it should be professional, wellness oriented and modern.

Target Market(s)

Private clients, governments, corporations. Luxury and high market.

Industry/Entity Type

Health And Wellness

Contact Information for Business Card

Dorian Vitality should be the logo

Colors

Designer to choose colors to be used in the design.

Requirements
Must have
• Dorian Vitality
• Name: Tomás Lirandel
• Wellness Coach, Consultant & Trainer.
• Website: www.dorianvitality-example.com
• Phone:
• Spain (+34) 612 480 317
• (USA) +1 (555) 610 4829
Nice to have
• The most important is the design of "Dorian Vitality", as this is going to be my personal brand logo. It should be professional, wellness, high end and actual.
Should not have
• no golds, no baroque style..

```html
<!DOCTYPE html>
<html lang="en">
<head>
<meta charset="utf-8">
<title>Dorian Vitality — Business Card</title>
<link rel="stylesheet" href="https://fonts.googleapis.com/css2?family=Montserrat:wght@300;400;500&family=Parisienne&family=Inter:ital,wght@0,400;1,400&display=swap">
<style>
  :root {
    --backdrop: #d8d3cb;
    --card-yellow: #e8e67b;
    --card-paper: #ecebec;
    --slate: #424e55;
    --teal: #86b7c1;
    --mist-grey: #7e8e98;
    --white: #ffffff;
  }
  * { margin: 0; padding: 0; box-sizing: border-box; }
  html, body {
    width: 1200px;
    height: 1200px;
    overflow: hidden;
    background: var(--backdrop);
  }
  .canvas {
    position: relative;
    width: 1200px;
    height: 1200px;
  }
  .card {
    position: absolute;
    left: 175px;
    width: 850px;
    height: 472px;
    overflow: hidden;
    box-shadow: 0 3px 8px rgba(0,0,0,0.18);
  }
  .card-front {
    top: 80px;
    background: var(--card-yellow);
  }
  .website {
    position: absolute;
    left: 0;
    right: 0;
    top: 231px;
    transform: translateY(-50%);
    text-align: center;
    font-family: "Montserrat", sans-serif;
    font-weight: 400;
    font-size: 36px;
    letter-spacing: 2px;
    color: var(--white);
  }
  .card-back {
    top: 648px;
    background: var(--card-paper);
  }
  .brand {
    position: absolute;
    left: 37px;
    top: 91px;
    transform: translateY(-50%);
    display: flex;
    align-items: center;
    gap: 22px;
  }
  .brand-dot {
    width: 58px;
    height: 58px;
    border-radius: 50%;
    background: var(--teal);
  }
  .brand-name {
    font-family: "Montserrat", sans-serif;
    font-weight: 500;
    font-size: 30px;
    letter-spacing: 3px;
    text-transform: uppercase;
    color: var(--slate);
  }
  .person {
    position: absolute;
    right: 90px;
    top: 196px;
    text-align: right;
  }
  .person-name {
    font-family: "Parisienne", cursive;
    font-size: 60px;
    line-height: 1;
    color: var(--slate);
  }
  .person-role {
    margin-top: 8px;
    margin-right: 19px;
    font-family: "Montserrat", sans-serif;
    font-weight: 400;
    font-size: 18px;
    letter-spacing: 2.5px;
    color: var(--mist-grey);
  }
  .contact-band {
    position: absolute;
    left: 0;
    right: 0;
    bottom: 0;
    height: 87px;
    background: var(--slate);
    border-top: 6px solid var(--card-yellow);
    display: flex;
    align-items: center;
    padding-left: 118px;
    padding-bottom: 12px;
    gap: 52px;
    font-family: "Inter", sans-serif;
    font-size: 20px;
    letter-spacing: 1.8px;
    color: var(--white);
  }
  .contact-item .region {
    font-style: italic;
    color: var(--card-yellow);
    margin-right: 12px;
  }
</style>
</head>
<body>
<main class="canvas">
  <section class="card card-front">
    <p class="website">www.dorianvitality-example.com</p>
  </section>

  <section class="card card-back">
    <div class="brand">
      <span class="brand-dot" aria-hidden="true"></span>
      <span class="brand-name">Dorian Vitality</span>
    </div>

    <div class="person">
      <p class="person-name">Tomás Lirandel</p>
      <p class="person-role">Wellness Coach, Consultant &amp; Trainer</p>
    </div>

    <div class="contact-band">
      <p class="contact-item"><span class="region">Spain.</span>(+34) 612 480 317</p>
      <p class="contact-item"><span class="region">USA.</span>+1 (555) 610 4829</p>
    </div>
  </section>
</main>
</body>
</html>
```